Business Card for Polygraph business in Africa

Business Card . Polygraph Examiner based in Tanzania, East Africa.
Business Card will be used to disseminate contact information to potential clients.
It should convey that I am a professional specifically in the polygraph field and perform my work with integrity.

I have attached the business card that I'm currently using, which I threw together myself initially. It's not professional enough.

Target Market(s)

Banks, Accounting Firms, Government Ministries, Gas, Oil, & Gemstone Mining Concerns, Wildlife Conservation NGOs, International companies located in East Africa.

Industry/Entity Type

Business

Contact Information for Business Card

Veritrace Kilonga
Miriam Holloway
PO Box 48317
Arusha, Tanzania
+255 612 839 274
miriamholloway@postvale.example

Colors
00a990
f37122
faa54b

Requirements
Must have
• - Veritrace Kilonga (with the word "Polygraph" being more prominent than the word "Tanzania")
• - Forensic Examinations
• - Employment Screening
• - Should contain a logo of the Continental Truthline Society (of which I'm a member)
• - I would like an accent design (such as the polygraph "squiggles" of a cardio tracing or such as that)
• - My contact information (less prominent, but large enough to read legibly). I would also consider putting the contact information on the second side of the card.
Nice to have
• My color suggestions are changeable.
Should not have
• Anything "cutesy" or "cartoonish"

```html
<!DOCTYPE html>
<html lang="en">
<head>
<meta charset="utf-8">
<title>Veritrace Kilonga – Business Card</title>
<link href="https://fonts.googleapis.com/css2?family=Jost:wght@300;400;500;600&display=swap" rel="stylesheet">
<style>
  :root {
    --page-bg: #ecebe8;
    --teal: #0b7a70;
    --teal-deep: #066b62;
    --slate: #2f3c41;
    --paper: #ffffff;
    --ink-soft: #5f6b6e;
    --badge-ring: #3a3f9a;
  }
  * { box-sizing: border-box; margin: 0; padding: 0; }
  html, body { width: 1200px; height: 886px; overflow: hidden; }
  body {
    background: var(--page-bg);
    font-family: "Jost", "Futura", sans-serif;
    position: relative;
  }
  .card {
    position: absolute;
    border-radius: 26px;
    overflow: hidden;
    box-shadow: 0 10px 28px rgba(0,0,0,.18);
  }

  /* Front: contact side */
  .card-front {
    left: 150px; top: 143px;
    width: 360px; height: 600px;
    background: linear-gradient(160deg, var(--teal) 0%, var(--teal-deep) 100%);
    color: var(--paper);
    text-align: center;
  }
  .member-badge {
    display: block;
    margin: 44px auto 0;
    width: 76px; height: 76px;
  }
  .holder-name {
    margin-top: 22px;
    font-size: 25px;
    font-weight: 600;
    letter-spacing: 1px;
    text-transform: uppercase;
  }
  .holder-firm {
    font-size: 19px;
    font-weight: 300;
    letter-spacing: .5px;
    opacity: .85;
  }
  .divider {
    width: 48px; height: 1px;
    margin: 16px auto 14px;
    background: var(--paper);
    opacity: .8;
  }
  .contact-lines {
    font-size: 15px;
    font-weight: 400;
    line-height: 1.55;
    list-style: none;
  }
  .base-band {
    position: absolute;
    left: 0; right: 0; bottom: 0;
    height: 200px;
    background: var(--slate);
    border-top: 6px solid var(--paper);
  }

  /* Back: brand side */
  .card-back {
    left: 560px; top: 263px;
    width: 560px; height: 360px;
    background: var(--paper);
    color: var(--teal);
  }
  .brand-lockup {
    position: absolute;
    left: 0; right: 0; top: 118px;
    display: flex;
    align-items: center;
    justify-content: center;
    gap: 18px;
  }
  .brand-dot {
    width: 58px; height: 58px;
    border: 5px solid var(--teal);
    border-radius: 50%;
  }
  .brand-name {
    font-size: 40px;
    font-weight: 500;
    color: var(--teal);
    letter-spacing: .5px;
  }
  .services {
    position: absolute;
    left: 0; right: 0; bottom: 44px;
    text-align: center;
    font-size: 15px;
    font-weight: 400;
    letter-spacing: 1px;
    color: var(--ink-soft);
  }
</style>
</head>
<body>
  <section class="card card-front">
    <svg class="member-badge" viewBox="0 0 76 76" role="img" aria-label="Continental Truthline Society membership seal">
      <circle cx="38" cy="38" r="36" fill="#ffffff"/>
      <circle cx="38" cy="38" r="31" fill="none" stroke="var(--badge-ring)" stroke-width="2"/>
      <circle cx="38" cy="38" r="20" fill="none" stroke="var(--badge-ring)" stroke-width="1"/>
    </svg>
    <h1 class="holder-name">Miriam Holloway</h1>
    <p class="holder-firm">Veritrace Kilonga</p>
    <div class="divider"></div>
    <ul class="contact-lines">
      <li>PO Box 48317, Arusha, Tanzania</li>
      <li>+255 612 839 274</li>
      <li>miriamholloway@postvale.example</li>
      <li>www.miriamholloway.example</li>
    </ul>
    <div class="base-band"></div>
  </section>

  <section class="card card-back">
    <div class="brand-lockup">
      <span class="brand-dot"></span>
      <span class="brand-name">Veritrace Kilonga</span>
    </div>
    <p class="services">Forensic Examinations &nbsp;|&nbsp; Employment Screening</p>
  </section>
</body>
</html>
```